TL - business card

Tallow Partners is an insurance brokerage firm, inovative, proactive, vigorous, which aims to become the leader of the insurance brokers in Anfrica. We should like to get some designs which should be avoided also in Gray / Metallic for the Administration and Orange / Blue for the Managers (ike in the picture sent). The Blue / Green logo is not the correct one, but the source of the file. Please adjust the color accordingly for the business cards. 1 / Orange / Blue 2 / Gray / Metallic We want something classic but which is transmitted strenght, inovation, modernity and most of all, rapidity. We want something start-up like, very punchy and catching eye remaining profesional at the same time. Name: Dorian Whitlock Function: Managing Director Address: N ° 17/18 Rua Veloso - R / C 2B Direita - Bairro Mutamba - Luanda Tel: (+244) 947 582 316 Email: dorian.whitlock@tallow-p.example Website: www.tallow-p. example We want classic in the front and creative, colorfull at the back. The cards will be printed in relief, with very high quality of paper.
Insurance Broker
Colors
Designer to choose colors to be used in the design.

```html
<!DOCTYPE html>
<html lang="en">
<head>
<meta charset="utf-8">
<title>Tallow Partners – Business Card</title>
<link rel="stylesheet" href="https://fonts.googleapis.com/css2?family=Montserrat:wght@400;500;700&display=swap">
<style>
  :root {
    --page-bg: #2a2a2a;
    --card-front: #f3f3f3;
    --brand-blue: #26aae1;
    --brand-green: #1a9a48;
    --text-grey: #5a5a5a;
    --white: #ffffff;
  }
  * { margin: 0; padding: 0; box-sizing: border-box; }
  html, body {
    width: 1200px; height: 900px; overflow: hidden;
    background: var(--page-bg);
    font-family: "Montserrat", sans-serif;
  }
  .canvas { position: relative; width: 1200px; height: 900px; }
  .card {
    position: absolute; left: 261px; width: 656px; height: 357px;
    overflow: hidden;
  }
  .card--front { top: 69px; background: var(--card-front); }
  .card--back { top: 472px; background: var(--brand-blue); }

  .brand { position: absolute; display: flex; flex-direction: column; align-items: center; }
  .card--front .brand { left: 27px; top: 30px; width: 232px; }
  .brand__dot { width: 58px; height: 58px; border-radius: 50%; background: var(--brand-green); margin-bottom: 18px; }
  .brand__name { font-weight: 700; font-size: 19px; letter-spacing: 0.5px; color: var(--brand-green); white-space: nowrap; }

  .contact { position: absolute; left: 28px; top: 160px; width: 262px; color: var(--text-grey); z-index: 1; }
  .contact__name { font-size: 24px; font-weight: 500; color: var(--brand-blue); letter-spacing: 0.5px; line-height: 1.2; white-space: nowrap; }
  .contact__role { font-size: 14px; margin-top: 4px; }
  .contact__address { font-size: 14px; line-height: 20px; margin-top: 16px; }
  .contact__lines { list-style: none; margin-top: 10px; font-size: 13px; line-height: 20px; }
  .contact__lines li { display: flex; align-items: center; gap: 9px; white-space: nowrap; }
  .contact__lines svg { width: 11px; height: 11px; flex: none; }

  .hero-art {
    position: absolute; left: 300px; top: 0; width: 356px; height: 357px;
    background: linear-gradient(135deg, rgba(38,170,225,0.9) 0%, rgba(38,170,225,0.65) 60%, rgba(26,154,72,0.75) 100%);
    clip-path: polygon(62% 0, 100% 0, 100% 45%, 55% 100%, 0 100%, 18% 55%);
  }

  .card--back .brand { left: 0; top: 105px; width: 656px; }
  .card--back .brand__dot { width: 76px; height: 76px; background: var(--white); margin-bottom: 22px; }
  .card--back .brand__name { color: var(--white); font-size: 24px; }
</style>
</head>
<body>
<main class="canvas">
  <section class="card card--front">
    <div class="brand">
      <div class="brand__dot"></div>
      <div class="brand__name">TALLOW PARTNERS</div>
    </div>
    <div class="hero-art" role="img" aria-label="Large brand symbol decoration in blue and green"></div>
    <div class="contact">
      <h1 class="contact__name">Dorian Whitlock</h1>
      <p class="contact__role">Managing Director</p>
      <p class="contact__address">N ° 17/18 Rua Veloso<br>R / C 2B Direita<br>Bairro Mutamba - Luanda</p>
      <ul class="contact__lines">
        <li>
          <svg viewBox="0 0 12 12" aria-hidden="true"><path d="M2.5 1 L4.5 1 L5 3.5 L3.8 4.5 Q5 7 7.5 8.2 L8.5 7 L11 7.5 L11 9.5 Q10.5 11 9 11 Q1 10 1 3 Q1 1.5 2.5 1 Z" fill="var(--brand-blue)"/></svg>
          +244 947 582 316
        </li>
        <li>
          <svg viewBox="0 0 12 12" aria-hidden="true"><rect x="1" y="2.5" width="10" height="7" rx="1" fill="none" stroke="var(--brand-blue)" stroke-width="1.4"/><path d="M1.5 3 L6 6.5 L10.5 3" fill="none" stroke="var(--brand-blue)" stroke-width="1.4"/></svg>
          dorian.whitlock@tallow-p.example
        </li>
      </ul>
    </div>
  </section>

  <section class="card card--back">
    <div class="brand">
      <div class="brand__dot"></div>
      <div class="brand__name">TALLOW PARTNERS</div>
    </div>
  </section>
</main>
</body>
</html>
```